Deskside Thrive Fliers and logo design

We need to design a product logo and some informational fliers for a vigour quest.
I have attached our Deskside Thrive logo - colours need to be complimentary but not the same, we would like fresh, funky but still professional. We generally communicate in a fairly casual way to reach our market. (We don't like boring)
Clear and simple - not too busy
images are good but not actual photos
Here is our website to give you an idea www.desksidethrive.co.nz
The flier is a 3 page document.
The logo is to say Vigour Quest. The challenge is based on exercise, connecting with people, giving, learning and taking notice (The 7 paths to flourishing) Once agin the logo needs to be complementary but not the same.
The Deskside thrive logo needs to be on the fliers but the vigour quest logo is separate.
Thanks very much!!

```html
<!DOCTYPE html>
<html lang="en">
<head>
<meta charset="utf-8">
<title>Deskside Thrive – Flier Set</title>
<link href="https://fonts.googleapis.com/css2?family=Montserrat:wght@700;800&family=Open+Sans:wght@400;600;700&display=swap" rel="stylesheet">
<style>
:root{
  --stage:#c8c8c8;
  --paper:#f3f3f3;
  --orange:#e0573a;
  --teal:#5cc4a9;
  --ink:#333;
  --list-box:#e4e4e4;
}
*{box-sizing:border-box;margin:0;padding:0}
html,body{width:1200px;height:1200px;overflow:hidden}
body{background:var(--stage);font-family:"Open Sans",sans-serif;color:var(--ink);position:relative}
.page{position:absolute;width:411px;height:532px;background:linear-gradient(#fff,var(--paper));overflow:hidden}
.page--stop{left:415px;top:54px}
.page--values{left:173px;top:610px}
.page--tips{left:621px;top:610px}
.abs{position:absolute}
.brand{position:absolute;left:19px;top:30px;display:flex;align-items:flex-start;gap:6px}
.brand__name{font-family:"Montserrat",sans-serif;font-weight:700;color:var(--teal);font-size:25px;line-height:24px;letter-spacing:-.3px}
.brand__dot{width:14px;height:14px;border-radius:50%;background:var(--orange);margin-top:2px}
.site-btn{position:absolute;z-index:3;height:28px;width:212px;border-radius:14px;background:var(--orange);color:#fff;font-family:"Montserrat",sans-serif;font-weight:700;font-size:12px;display:flex;align-items:center;justify-content:center}
.photo{position:absolute;z-index:0}
/* stop page */
.hero-photo{left:319px;top:6px;width:90px;height:90px;border-radius:50%;background:radial-gradient(circle at 40% 35%,#f6e2c0,#c89b5c 70%,#8a6a3a)}
.circle-orange{left:288px;top:-30px;width:66px;height:66px;border-radius:50%;background:var(--orange)}
.circle-teal{left:352px;top:78px;width:49px;height:49px;border-radius:50%;background:var(--teal)}
.headline{position:absolute;left:0;width:411px;text-align:center}
.headline--soft{top:122px;color:var(--orange);font-family:"Montserrat",sans-serif;font-weight:700;font-size:10.5px}
.headline--loud{top:138px;color:var(--teal);font-family:"Montserrat",sans-serif;font-weight:800;font-size:13.5px;letter-spacing:.2px}
.step-tag{position:absolute;z-index:2;left:17px;width:96px;height:20px;background:var(--orange);color:#fff;font-family:"Montserrat",sans-serif;font-weight:800;font-size:11px;line-height:20px;padding-left:5px;clip-path:polygon(0 0,100% 0,88% 100%,0 100%)}
.step-text{position:absolute;z-index:2;left:17px;width:200px;font-size:5.6px;line-height:8px}
.step-text b{font-weight:700}
.intro{position:absolute;z-index:2;left:224px;top:161px;width:172px;font-size:6.9px;line-height:10px;text-align:justify}
.intro p{margin-bottom:10px}
.scene-photo{left:0;top:380px;width:411px;height:152px;background:linear-gradient(to bottom,rgba(243,243,243,0) 0%,rgba(214,170,120,.6) 35%,#9a6a44 72%,#5a3c2a)}
/* shared bottom pages */
.banner{position:absolute;left:190px;top:27px;width:221px;background:var(--teal);color:#fff;padding:6px 10px}
.banner__title{font-family:"Montserrat",sans-serif;font-weight:800;font-size:16px;line-height:18px}
.banner__sub{font-size:5.4px;line-height:7px;margin-top:3px}
.section-title{position:absolute;left:15px;color:var(--orange);font-family:"Montserrat",sans-serif;font-weight:700;font-size:7.5px}
.section-text{position:absolute;left:15px;width:380px;font-size:5.5px;line-height:7px}
.values-box{position:absolute;left:15px;top:134px;width:381px;height:238px}
.values-col{position:absolute;top:10px;list-style:none;font-size:5.6px;line-height:8.05px;font-weight:600}
.answer{position:absolute;font-size:8px;font-weight:700;color:var(--orange);display:flex;align-items:flex-end;gap:4px;width:180px}
.answer span.line{flex:1;border-bottom:.8px solid #555;height:1px;margin-bottom:2px}
.tips-lead{position:absolute;left:0;top:102px;width:411px;height:64px;background:var(--orange);color:#fff;font-size:11.3px;line-height:15px;padding:9px 15px}
.tips{position:absolute;z-index:2;left:16px;top:196px;width:380px;list-style:none;font-size:6px;line-height:8.3px}
.tips li{margin-bottom:4.2px}
.tips b{font-weight:700}
.family-photo{left:0;top:420px;width:411px;height:112px;background:linear-gradient(to bottom,rgba(243,243,243,0),#e9ddd2 45%,#d9c2ad)}
</style>
</head>
<body>

<!-- Page 1: S.T.O.P -->
<section class="page page--stop">
  <div class="photo scene-photo" role="img" aria-label="Mother and daughter playing in a blanket fort with fairy lights"></div>
  <div class="brand"><div class="brand__name">deskside<br>thrive</div><div class="brand__dot"></div></div>
  <div class="photo circle-orange"></div>
  <div class="photo circle-teal"></div>
  <div class="photo hero-photo" role="img" aria-label="Family running with a kite in a sunny field"></div>

  <p class="headline headline--soft">We cannot control what happens to us in life,</p>
  <p class="headline headline--loud">BUT WE CAN CHANGE THE WAY WE REACT</p>

  <div class="step-tag" style="top:161px">S = Stop</div>
  <p class="step-text" style="top:184px">Stop what you are doing: Press the pause button on your thoughts and actions.</p>
  <div class="step-tag" style="top:206px">T = Take</div>
  <p class="step-text" style="top:229px">Take a few deep breaths to centre yourself and bring yourself fully into the present moment.</p>
  <div class="step-tag" style="top:251px;width:118px">O = Observe</div>
  <p class="step-text" style="top:274px">Observe what is going on with your:<br><b>1.Body</b><br>What physical sensations are you aware of (touch, sight, hearing, taste, smell)?<br><b>Emotions</b><br>What are you feeling right now?<br><b>2.Mind</b><br>What assumptions are your making about your feelings? What is the story you're telling yourself about why you are having them?</p>
  <div class="step-tag" style="top:351px;width:118px">P = Proceed</div>
  <p class="step-text" style="top:376px">Proceed with whatever you were doing, making a conscious, intentional choice to incorporate what you just learned.</p>

  <div class="intro">
    <p>Stress happens because we are allowing fear, anger, disappointment and a host of other negative emotions to navigate our actions. By becoming aware of these emotions and allowing them to simply be, we can begin to gain control of how we react and respond to stressful situations.</p>
    <p>Our experience is always changing. Without awareness, mental patterns related to what we fear and what upsets us make life harder.</p>
    <p>S.T.O.P is a powerful, yet surprisingly basic strategy that helps you to be focused, alert, relaxed and at your emotional best when stressful moments present themselves in your life.</p>
    <p>Simply put, it's a four-step checklist to use anytime you want to ground yourself and get some insight into whatever is going on. The whole idea behind it is that by taking a very brief break—even less than one minute—you can determine the very best action to take in the moment.</p>
  </div>

  <div class="site-btn" style="left:109px;top:488px">desksidethrive.co.nz</div>
</section>

<!-- Page 2: Values -->
<section class="page page--values">
  <div class="brand"><div class="brand__name">deskside<br>thrive</div><div class="brand__dot"></div></div>
  <div class="banner">
    <div class="banner__title">Values</div>
    <p class="banner__sub">This exercise is designed to help you reach a better understanding of your most significant values.</p>
  </div>

  <h2 class="section-title" style="top:101px">Step 1: What I Value Most…</h2>
  <p class="section-text" style="top:111px">From this list of values (both work and personal), select the ten that are most important to you - as guides for how to behave, or as components of a valued way of life. Feel free to add any values of your own to this list.</p>

  <div class="values-box">
    <svg class="abs" width="381" height="238" viewBox="0 0 381 238"><polygon points="0,0 362,0 381,19 381,238 0,238" fill="#e4e4e4"/><line x1="147" y1="12" x2="147" y2="228" stroke="#555" stroke-width=".6"/><line x1="255" y1="12" x2="255" y2="228" stroke="#555" stroke-width=".6"/></svg>
    <ul class="values-col" style="left:27px">
      <li>Achievement</li><li>Advancement and promotion</li><li>Adventure</li><li>Affection (love and caring)</li><li>Arts</li><li>Challenging problems</li><li>Change and variety</li><li>Close relationships</li><li>Community</li><li>Competence</li><li>Competition</li><li>Cooperation</li><li>Country</li><li>Creativity</li><li>Decisiveness</li><li>Democracy</li><li>Ecological awareness</li><li>Economic security</li><li>Effectiveness</li><li>Efficiency</li><li>Ethical practice</li><li>Excellence</li><li>Excitement</li><li>Fame</li><li>Fast living</li><li>Financial gain</li><li>Freedom</li>
    </ul>
    <ul class="values-col" style="left:150px">
      <li>Friendships</li><li>Growth</li><li>Having a family</li><li>Helping other people</li><li>Helping society</li><li>Honesty</li><li>Independence</li><li>Influencing others</li><li>Inner harmony</li><li>Integrity</li><li>Intellectual status</li><li>Involvement</li><li>Job tranquility</li><li>Knowledge</li><li>Leadership</li><li>Location</li><li>Loyalty</li><li>Market position</li><li>Meaningful work</li><li>Merit</li><li>Money</li><li>Nature</li><li>Being around people who</li><li>are open and honest</li><li>Order (tranquility,</li><li>stability, conformity)</li><li>Personal development</li>
    </ul>
    <ul class="values-col" style="left:259px">
      <li>Physical challenge</li><li>Pleasure</li><li>Power and authority</li><li>Privacy</li><li>Public service</li><li>Purity</li><li>Quality of what I take part in</li><li>Quality relationships</li><li>Recognition (respect from others, status)</li><li>Religion</li><li>Reputation</li><li>Responsibility and accountability</li><li>Security</li><li>Self-Respect</li><li>Serenity</li><li>Sophistication</li><li>Stability</li><li>Status</li><li>Supervising others</li><li>Time freedom</li><li>Truth</li><li>Wealth</li><li>Wisdom</li><li>Work under pressure</li><li>Work with others</li><li>Working alone</li>
    </ul>
  </div>

  <h2 class="section-title" style="top:379px">Step 2: Elimination</h2>
  <p class="section-text" style="top:389px">Now that you have identified ten, imagine that you are only permitted to have five values. Which five would you give up? Cross them off. Put them into order, the one that is most important to you first. Write it somewhere and refer to it when you can't make a decision, align yourself with what makes you feel good.</p>
  <div class="answer" style="left:15px;top:420px">1<span class="line"></span></div>
  <div class="answer" style="left:214px;top:420px">3<span class="line"></span></div>
  <div class="answer" style="left:15px;top:448px">2<span class="line"></span></div>
  <div class="answer" style="left:214px;top:448px">4<span class="line"></span></div>

  <h2 class="section-title" style="top:467px">Step 3: Support yourself</h2>
  <p class="section-text" style="top:477px">Write it somewhere and refer to it when you can't make a decision, align yourself with what makes you feel good.</p>

  <div class="site-btn" style="left:105px;top:492px">desksidethrive.co.nz</div>
</section>

<!-- Page 3: Tips -->
<section class="page page--tips">
  <div class="photo family-photo" role="img" aria-label="Laughing couple playing together at home"></div>
  <div class="brand"><div class="brand__name">deskside<br>thrive</div><div class="brand__dot"></div></div>
  <div class="banner" style="padding:10px 10px">
    <div class="banner__title" style="font-size:13.5px;line-height:17px">10 TIPS TO IMPROVE YOUR WELLBEING</div>
  </div>

  <p class="tips-lead">Yes, you will have to get off the couch and you might need to say no to burgers for lunch every day but we promise we won't turn you into lycra wearing vegans with prescriptions to Glowhaus!</p>

  <p class="abs" style="left:16px;top:178px;font-size:6.8px;font-weight:700">Small changes every day can make a huge difference.</p>

  <ol class="tips">
    <li><b>1. Put on your wake up grin</b> - Smile and think happy thoughts – that first 90 secs has a big impact on your day. If you start the day with bad thoughts, then it compounds – simply turn up the corners of your mouth you'll start to release endorphins and serotonin, your feel-good hormones.</li>
    <li><b>2. Drink lemon and warm water first thing</b> – and keep drinking water all day. It will cleanse your liver, you will eat less, you'll feel better and have a clearer head.</li>
    <li><b>3. Exercise</b> – it boosts the happy chemicals in your brain. So Be Active - get your heart rate going and stretch those muscles. At the very least take the stairs. To get your endorphins surging you'll need to really heavy breathe – so walk up those stairs faster, do your house work quicker – get that heart pumping.</li>
    <li><b>4. Eat a banana</b> – Did you ever see a depressed chimp? Bananas help to lessen feelings of stress and anxiety due to high levels of tryptophan which converts to serotonin – one of those happy hormone. The high level of potassium helps you to be more alert and will give you energy.</li>
    <li><b>5. Put on your WOW! Glasses</b> – Go outside and Take Notice – The wind, the warmth, the cold, the trees, the blossom, the amazing sky, the moon. The world is full of things that make you go WOW, if you just slow down and Take Notice. Even better, go with a friend and Connect as well.</li>
    <li><b>6. 5 fruit and veg per day</b> – Get the fibre into to you… Without it you clog up, if you clog up you get grumpy and sluggish, if you get grumpy and sluggish – let's not go there! If you have trouble fitting the veges in, put them into a smoothie.</li>
    <li><b>7. Play music</b> – it cheers you up. Create a playlist for when you need a pick-me-up. Play it in the car to and from work, doing your housework or when you're going for that brisk walk, getting out of breath and send even more happy hormones to your brain. (No, not the sad break-up playlist!)</li>
    <li><b>8. Remove a poison</b> – Take away something that you know is bad for you – fast food, sugar, gluten – even for a couple of days a week – replace it with something healthy like water, fruit, veg, quinoa, exercise whatever works for you.</li>
    <li><b>9. Kill em with kindness</b> – When you're feeling bad, do something nice for someone else and it will make their day and you'll feel even better. In fact, Give every day.</li>
    <li><b>10. Keep the cogs turning</b> – Use it or lose it as they say – use your brain. Keep learning – something new every day.</li>
  </ol>

  <div class="site-btn" style="left:96px;top:491px">desksidethrive.co.nz</div>
</section>

</body>
</html>
```